Corvane Holdings , new business card design

investment firm with corporate clients . need double sided business card , vertical and horizontal options ,logo must be clear. prefer pantone colors only and sharp design. website also www.corvane.ae

Khalid Bin Tarrafi
Managing Director
Tel. +971 4 387 2940
Mobile +971 50 518 2403
khalid@corvane.ae
Q-Span Plaza, officw 18-B07, Warqa Gardens, Dubai

Contact Information for Business Card

Khalid Bin Tarrafi
Managing Director

Font styles to use
Serif

Colors

Designer to choose colors to be used in the design.

```html
<!DOCTYPE html>
<html lang="en">
<head>
<meta charset="utf-8">
<title>Corvane Holdings – Business Card</title>
<link rel="stylesheet" href="https://fonts.googleapis.com/css2?family=Roboto:wght@300;400&family=Roboto+Condensed:wght@500&display=swap">
<style>
  :root {
    --brand-blue: #436d91;
    --paper: #f7f7f7;
    --backdrop: #dcdcdc;
    --ink: #1f1f1f;
    --ink-soft: #555555;
    --rule: #9a9a9a;
    --white: #ffffff;
  }
  * { margin: 0; padding: 0; box-sizing: border-box; }
  html, body {
    width: 1200px; height: 960px; overflow: hidden;
    background: var(--backdrop);
    font-family: "Roboto", Arial, sans-serif;
  }
  .canvas { position: relative; width: 1200px; height: 960px; }

  .card { position: absolute; width: 601px; height: 342px; }
  .card--front { left: 314px; top: 113px; background: var(--paper); }
  .card--back { left: 311px; top: 472px; background: var(--brand-blue); }

  .wordmark {
    position: absolute;
    font-weight: 300;
    text-transform: uppercase;
    text-align: center;
    line-height: 1;
  }
  .wordmark__primary { display: block; font-size: 34px; letter-spacing: 0.28em; }
  .wordmark__secondary { display: block; font-size: 12px; letter-spacing: 0.62em; margin-top: 8px; }

  .card--front .wordmark { left: 40px; top: 138px; width: 260px; color: var(--ink); }
  .card--back .wordmark { left: 0; top: 140px; width: 600px; color: var(--white); }

  .divider {
    position: absolute; left: 318px; top: 85px;
    width: 1px; height: 157px; background: var(--rule);
  }

  .contact { position: absolute; left: 342px; top: 83px; }
  .contact__name {
    font-family: "Roboto Condensed", Arial, sans-serif;
    font-weight: 500; font-size: 21px; color: var(--brand-blue);
  }
  .contact__role { font-size: 14.5px; color: var(--ink); margin-top: 2px; }
  .contact__address { font-size: 14px; color: var(--ink-soft); line-height: 18px; margin-top: 12px; }
  .contact__list { list-style: none; margin-top: 11px; }
  .contact__item {
    display: flex; align-items: center; gap: 7px;
    font-size: 14px; color: var(--ink); height: 19px;
  }
  .contact__icon { width: 13px; height: 13px; fill: var(--brand-blue); flex: none; }

  .web-band {
    position: absolute; left: 0; top: 299px;
    width: 100%; height: 27px; background: var(--brand-blue);
    display: flex; align-items: center; justify-content: center;
  }
  .web-address {
    color: var(--white); font-size: 14px; letter-spacing: 0.42em; font-weight: 400;
  }
  .card--back .web-address {
    position: absolute; left: 0; top: 289px; width: 600px; text-align: center;
  }
</style>
</head>
<body>
<main class="canvas">

  <section class="card card--front" aria-label="Business card front">
    <div class="wordmark">
      <span class="wordmark__primary">Corvane</span>
      <span class="wordmark__secondary">Holdings</span>
    </div>

    <div class="divider"></div>

    <div class="contact">
      <p class="contact__name">Khalid Bin Tarrafi</p>
      <p class="contact__role">Managing Director</p>
      <p class="contact__address">Q-Span Plaza, officw 18-B07<br>Warqa Gardens, Dubai</p>
      <ul class="contact__list">
        <li class="contact__item">
          <svg class="contact__icon" viewBox="0 0 24 24" aria-hidden="true"><path d="M6.6 10.8c1.4 2.8 3.8 5.1 6.6 6.6l2.2-2.2c.3-.3.7-.4 1-.2 1.1.4 2.3.6 3.6.6.6 0 1 .4 1 1V20c0 .6-.4 1-1 1C10.6 21 3 13.4 3 4c0-.6.4-1 1-1h3.5c.6 0 1 .4 1 1 0 1.3.2 2.5.6 3.6.1.3 0 .7-.2 1z"/></svg>
          +971 4 387 2940
        </li>
        <li class="contact__item">
          <svg class="contact__icon" viewBox="0 0 24 24" aria-hidden="true"><path d="M7 1h10a2 2 0 0 1 2 2v18a2 2 0 0 1-2 2H7a2 2 0 0 1-2-2V3a2 2 0 0 1 2-2zm0 3v14h10V4zm5 15.5a1 1 0 1 0 0 2 1 1 0 0 0 0-2z"/></svg>
          +971 50 518 2403
        </li>
        <li class="contact__item">
          <svg class="contact__icon" viewBox="0 0 24 24" aria-hidden="true"><path d="M2 5h20v14H2zm2 2v.5l8 5 8-5V7l-8 5z"/></svg>
          khalid@corvane.ae
        </li>
      </ul>
    </div>

    <div class="web-band"><span class="web-address">www.corvane.ae</span></div>
  </section>

  <section class="card card--back" aria-label="Business card back">
    <div class="wordmark">
      <span class="wordmark__primary">Corvane</span>
      <span class="wordmark__secondary">Holdings</span>
    </div>
    <p class="web-address">www.corvane.ae</p>
  </section>

</main>
</body>
</html>
```